Stylish business cards for KV7

To create an appealing and professional business card design for a WOMEN Owned Construction Supply Company.
2 sided card. Incorporate brand elements, curvy, colorful, sleek and bright. No solid white background. attached samples of styles added shapes/ribbons. Want something with that WOW that looks awesome, factor. It is a new logo, so feel free to mess with logo colors in the blue and teal factors that can look good with both dark and light background. If you want to try a watermark with just the KV7, without the "Supply" that might look cool to.

Industry/Entity Type

Women owned construction supply company

Contact Information for Business Card

Name, Title, and phone number and email, web page. maybe spot for qr code.

Font styles to use
Sans Serif

Requirements
Nice to have
• would love to see colors, maybe stylish ribbon dividers or some sort of 2 or 3 tone color card that compliments logo.
Should not have
• Please do not have all white background. Do not include Home/reale state/ or building images.

```html
<!DOCTYPE html>
<html lang="en">
<head>
<meta charset="utf-8">
<title>KV7 Supply – Business Cards</title>
<link href="https://fonts.googleapis.com/css2?family=Montserrat:wght@400;700&display=swap" rel="stylesheet">
<style>
  :root {
    --backdrop: #1a1a1a;
    --card: #1b3556;
    --teal: #2a94c0;
    --ink: #eef2f6;
    --rule: #2a8fb8;
  }
  * { box-sizing: border-box; margin: 0; padding: 0; }
  html, body {
    width: 1200px;
    height: 1059px;
    overflow: hidden;
    background: var(--backdrop);
    font-family: "Montserrat", sans-serif;
    color: var(--ink);
  }
  .card {
    position: absolute;
    background: var(--card);
    border-radius: 18px;
  }
  .card--front { left: 257px; top: 89px; width: 687px; height: 390px; }
  .card--back  { left: 254px; top: 547px; width: 693px; height: 393px; }

  .brand-name {
    position: absolute;
    font-weight: 700;
    color: var(--ink);
    white-space: nowrap;
    letter-spacing: 0.5px;
  }
  .card--front .brand-name { right: 37px; top: 92px; font-size: 34px; }
  .card--back .brand-name {
    left: 0; right: 0; top: 166px;
    text-align: center;
    font-size: 58px;
  }

  .person { position: absolute; left: 37px; top: 184px; }
  .person__name {
    font-size: 23px;
    font-weight: 700;
    color: var(--teal);
    letter-spacing: 0.3px;
    line-height: 1;
  }
  .person__title { font-size: 15px; margin-top: 6px; line-height: 1; }

  .divider {
    position: absolute;
    left: 37px; top: 252px;
    width: 613px; height: 1px;
    background: var(--rule);
  }

  .contacts {
    position: absolute;
    left: 37px; top: 279px;
    list-style: none;
    font-size: 15.5px;
  }
  .contacts li {
    display: flex;
    align-items: center;
    height: 27px;
  }
  .contacts svg { width: 13px; height: 13px; margin-right: 7px; flex: none; }

  .address {
    position: absolute;
    right: 37px; top: 307px;
    text-align: right;
    font-size: 15.5px;
    line-height: 24px;
    font-style: normal;
  }
</style>
</head>
<body>
  <section class="card card--front">
    <div class="brand-name">KV7 Supply</div>

    <div class="person">
      <div class="person__name">DANA WHITFIELD</div>
      <div class="person__title">CEO/Founder</div>
    </div>

    <div class="divider"></div>

    <ul class="contacts">
      <li>
        <svg viewBox="0 0 24 24" aria-hidden="true"><path fill="var(--teal)" d="M6.6 10.8a15 15 0 0 0 6.6 6.6l2.2-2.2c.3-.3.7-.4 1-.2 1.1.4 2.3.6 3.6.6.6 0 1 .4 1 1V20c0 .6-.4 1-1 1A17 17 0 0 1 3 4c0-.6.4-1 1-1h3.5c.6 0 1 .4 1 1 0 1.3.2 2.5.6 3.6.1.3 0 .7-.2 1z"/></svg>
        555.014.2287
      </li>
      <li>
        <svg viewBox="0 0 24 24" aria-hidden="true"><path fill="var(--teal)" d="M2 5h20v14H2z"/><path fill="none" stroke="var(--card)" stroke-width="1.8" d="M2 5l10 8 10-8M2 19l7-7M22 19l-7-7"/></svg>
        info@kv7supply.com.au
      </li>
      <li>
        <svg viewBox="0 0 24 24" aria-hidden="true"><g fill="none" stroke="var(--teal)" stroke-width="2"><circle cx="12" cy="12" r="10"/><ellipse cx="12" cy="12" rx="4.5" ry="10"/><path d="M2 12h20M4 7h16M4 17h16"/></g></svg>
        www.kv7supply.com.au
      </li>
    </ul>

    <address class="address">
      P.O Box 4120 Harbour Lane<br>
      Northvale AB 10234
    </address>
  </section>

  <section class="card card--back">
    <div class="brand-name">KV7 Supply</div>
  </section>
</body>
</html>
```